Business Card Design Project

After recently finishing a design project for the company logo using markbazaar, it's now time for a business card. Attached to this is the logo.

The requirements for the business card are pretty straightforward:

- A clean, uncomplicated look
- Consistent usage of fonts
- Designs for both single sided and double sided cards
- A modern layout with preferably space to refer to social media accounts and/or downloadable vcards through a qr code
- consistent application of the company colour scheme: red/white. Hex codes for exact colour can be provided

Thanks!

```html
<!DOCTYPE html>
<html lang="en">
<head>
<meta charset="utf-8">
<title>Ember Block Staffing – Business Card</title>
<link href="https://fonts.googleapis.com/css2?family=PT+Sans:ital,wght@0,400;0,700;1,700&display=swap" rel="stylesheet">
<style>
  :root {
    --backdrop: #b07c50;
    --card-white: #ffffff;
    --card-black: #1a1716;
    --brand-red: #e02127;
    --ink-dark: #231f20;
    --ink-body: #3a3536;
    --tint-red: #fbe4da;
    --shadow: rgba(0, 0, 0, 0.35);
  }
  * { margin: 0; padding: 0; box-sizing: border-box; }
  html, body { width: 960px; height: 1200px; overflow: hidden; }
  body {
    background: var(--backdrop);
    font-family: "PT Sans", sans-serif;
    position: relative;
  }
  .card {
    position: absolute;
    width: 840px;
    height: 480px;
    border-radius: 30px;
    box-shadow: 2px 4px 8px var(--shadow);
    overflow: hidden;
  }
  .card--front { left: 60px; top: 83px; background: var(--card-white); }
  .card--back { left: 55px; top: 638px; background: var(--card-black); }

  .brand {
    position: absolute;
    display: flex;
    align-items: center;
    gap: 18px;
  }
  .brand__square {
    width: 52px;
    height: 52px;
    background: var(--brand-red);
    flex: none;
  }
  .brand__name {
    font-weight: 700;
    font-size: 52px;
    letter-spacing: -0.5px;
    white-space: nowrap;
    line-height: 1;
  }
  .card--front .brand { left: 32px; top: 64px; }
  .card--front .brand__name { color: var(--ink-dark); }
  .card--back .brand { left: 142px; top: 214px; }
  .card--back .brand__name { color: var(--card-white); font-size: 56px; }

  .backdrop-mark {
    position: absolute;
    left: 36px;
    top: 240px;
    width: 220px;
    height: 220px;
    background: var(--tint-red);
  }

  .contact {
    position: absolute;
    right: 30px;
    top: 186px;
    text-align: right;
    color: var(--ink-body);
    font-size: 23px;
    line-height: 1.3;
  }
  .contact__name {
    font-weight: 700;
    font-size: 31px;
    color: var(--ink-dark);
    line-height: 1.2;
  }
  .contact__role { margin-bottom: 18px; }
  .contact__line { margin-bottom: 9px; }
  .contact__label { font-weight: 700; font-style: italic; color: var(--ink-dark); }
  .contact__address { margin-top: 4px; line-height: 1.4; }
</style>
</head>
<body>
  <section class="card card--front" aria-label="Business card front">
    <div class="backdrop-mark" aria-hidden="true"></div>
    <div class="brand">
      <span class="brand__square" aria-hidden="true"></span>
      <span class="brand__name">Ember Block Staffing</span>
    </div>
    <div class="contact">
      <p class="contact__name">Your Name</p>
      <p class="contact__role">Designation</p>
      <p class="contact__line"><span class="contact__label">t</span> : 123-123-1234</p>
      <p class="contact__line"><span class="contact__label">e</span> : info@yourwebsite.com</p>
      <p class="contact__line"><span class="contact__label">w</span> : www.emberblock.com</p>
      <p class="contact__address">1234, Street Name, City<br>District, Country Code.</p>
    </div>
  </section>

  <section class="card card--back" aria-label="Business card back">
    <div class="brand">
      <span class="brand__square" aria-hidden="true"></span>
      <span class="brand__name">Ember Block Staffing</span>
    </div>
  </section>
</body>
</html>
```